food delivery web site design

Currently we have a smartphone app (ios/android) that is being used by our clients to make orders to about 30 different restaurants.

We would like to extent this and have also a website that is able to mimic the same functionalities:
- register
- show restaurants based on the selected address
- make order to an restaurant
- being able to process orders for other registered users (please read the attached doc for complete info on this)

Take a look at the attached doc for more info.

```html
<!DOCTYPE html>
<html lang="ro">
<head>
<meta charset="utf-8">
<title>Gustino – Ți-e foame?</title>
<link rel="stylesheet" href="https://fonts.googleapis.com/css2?family=Oswald:wght@400;500&family=Open+Sans:wght@400;600&display=swap">
<style>
:root{
  --red:#9b1308;
  --red-line:#c9463b;
  --yellow:#f3d765;
  --yellow-text:#9b1308;
  --ink:#231f1c;
  --muted:#5a5552;
  --tile:#1b1b1b;
  --footer:#222;
  --white:#fff;
}
*{margin:0;padding:0;box-sizing:border-box}
html,body{width:1200px;height:1108px;overflow:hidden;background:var(--white)}
body{position:relative;font-family:"Open Sans",sans-serif;color:var(--ink)}
.hero-bg{position:absolute;left:0;top:0;width:1200px;height:580px;
  background:
   linear-gradient(to bottom,rgba(255,255,255,0) 0%,rgba(255,255,255,0) 55%,#fff 100%),
   radial-gradient(ellipse at 20% 45%,#e9b8b0 0%,rgba(233,184,176,0) 45%),
   radial-gradient(ellipse at 60% 25%,#f0e3b4 0%,rgba(240,227,180,0) 45%),
   radial-gradient(ellipse at 90% 30%,#ead7a6 0%,rgba(234,215,166,0) 40%),
   linear-gradient(to bottom,#d9cfcb 0%,#f3ece6 60%,#fff 100%);}
.topbar{position:absolute;left:0;top:51px;width:1200px;height:54px;background:var(--red);
  border-top:1px solid var(--red-line);border-bottom:1px solid var(--red-line)}
.topbar::before,.topbar::after{content:"";position:absolute;left:0;right:0;height:1px;background:rgba(255,255,255,.25)}
.topbar::before{top:2px}.topbar::after{bottom:2px}
.rule{position:absolute;height:4px;border-top:1px solid rgba(255,255,255,.6);border-bottom:1px solid rgba(255,255,255,.6)}
.dots{position:absolute;left:612px;top:76px;width:275px;height:4px;border-top:1px dotted rgba(255,255,255,.6);border-bottom:1px dotted rgba(255,255,255,.6)}
.brand{position:absolute;left:150px;top:60px;display:flex;align-items:center;gap:8px;font-family:"Oswald",sans-serif;font-weight:500;font-size:26px;line-height:36px;color:var(--white)}
.brand-dot{width:14px;height:14px;border-radius:50%;background:var(--yellow)}
.call{position:absolute;left:350px;top:60px;font-family:"Oswald",sans-serif;font-size:25px;color:var(--white);letter-spacing:-.3px;line-height:36px;white-space:nowrap}
.call .phone{color:var(--yellow)}
.call svg{vertical-align:-3px;margin:0 2px 0 4px}
.auth{position:absolute;top:66px;font-family:"Oswald",sans-serif;font-size:15px;color:var(--white);line-height:24px;display:flex;align-items:center;gap:5px}
.hero-title{position:absolute;left:138px;top:204px;font-family:"Oswald",sans-serif;font-weight:400;font-size:34px;color:var(--ink);letter-spacing:-.5px}
.hero-sub{position:absolute;left:138px;top:256px;font-size:20.5px;color:var(--ink)}
.search{position:absolute;left:138px;top:311px;width:924px;height:122px;background:var(--red);border-bottom:2px solid var(--yellow)}
.search::before{content:"";position:absolute;inset:5px;border:1px solid rgba(255,255,255,.35)}
.label{position:absolute;top:19px;font-family:"Oswald",sans-serif;font-weight:500;font-size:15px;color:var(--white)}
.field{position:absolute;top:45px;height:50px;background:var(--white);font-family:"Oswald",sans-serif;font-size:19px;color:#6a6563;line-height:50px;padding-left:13px;white-space:nowrap;overflow:hidden}
.field svg{position:absolute;right:14px;top:21px}
.btn-show{position:absolute;left:795px;top:45px;width:102px;height:50px;background:var(--yellow);color:var(--yellow-text);font-family:"Oswald",sans-serif;font-weight:500;font-size:14px;line-height:18px;text-align:center;padding-top:7px}
.section-head{position:absolute;left:138px;top:469px;width:924px;height:5px;border-top:1px solid #9a9390;border-bottom:1px solid #9a9390}
.section-pill{position:absolute;left:496px;top:448px;width:209px;height:48px;background:var(--white);border-radius:10px;text-align:center;font-family:"Oswald",sans-serif;font-weight:400;font-size:18px;line-height:48px;color:var(--ink)}
.partners{position:absolute;left:138px;top:518px;width:924px;display:grid;grid-template-columns:repeat(5,129px);column-gap:70px;row-gap:42px}
.partner .thumb{width:129px;height:102px;background:var(--tile)}
.partner .name{margin-top:8px;font-size:14.5px;line-height:18px;color:var(--ink);white-space:nowrap}
.partner .cuisine{font-size:10.5px;line-height:14px;color:var(--muted);text-transform:uppercase;letter-spacing:.3px}
.footer{position:absolute;left:0;top:1051px;width:1200px;height:57px;background:var(--footer);border-top:3px solid #333;box-shadow:inset 0 2px 0 #fff}
.footer-nav{position:absolute;left:138px;top:18px;font-size:12.5px;color:var(--white)}
.footer-nav span{color:#666;margin:0 7px}
.copyright{position:absolute;right:138px;top:18px;font-size:12.5px;color:var(--white)}
</style>
</head>
<body>
<div class="hero-bg" role="img" aria-label="Fotografie cu deserturi: flan cu caramel, căpșuni și zmeură pe o farfurie albă"></div>

<header>
  <div class="topbar"></div>
  <div class="rule" style="left:0;top:76px;width:138px"></div>
  <div class="rule" style="left:272px;top:76px;width:62px"></div>
  <div class="rule" style="left:1064px;top:76px;width:136px"></div>
  <div class="dots"></div>
  <div class="brand"><span class="brand-dot"></span>Gustino</div>
  <div class="call">SUNĂ-NE LA<svg width="16" height="18" viewBox="0 0 16 18"><path d="M4 1 L7 5 L5 7 C6 10 8 12 10 13 L12 11 L15 14 L13 17 C7 17 1 10 1 4 Z" fill="#f3d765"/></svg><span class="phone">0700 123 456</span></div>
  <div class="auth" style="left:906px"><svg width="15" height="13" viewBox="0 0 15 13"><path d="M1 12 C1 6 5 4 9 4 V0 L15 6 L9 12 V8 C5 8 3 9 1 12Z" fill="#fff"/></svg>LOGIN</div>
  <div class="auth" style="left:981px"><svg width="16" height="13" viewBox="0 0 16 13"><circle cx="6" cy="3.5" r="3" fill="#fff"/><path d="M0 13 C0 8 3 7 6 7 C9 7 12 8 12 13Z" fill="#fff"/><path d="M13 2V7M10.5 4.5H15.5" stroke="#fff" stroke-width="1.6"/></svg>SIGN IN</div>
</header>

<main>
  <h1 class="hero-title">ȚI-E FOAME ?</h1>
  <p class="hero-sub">Comandă direct de pe mobil mancărurile favorite de la restaurantul tău preferat.</p>

  <form class="search">
    <div class="label" style="left:28px">INTRODU ADRESA</div>
    <div class="field" style="left:28px;width:534px">LOREM IPSUM DOLOR SIT AMET, CONSECTETUER ADIPISCING ELIT. AENEAN CO</div>
    <div class="label" style="left:581px">ALEGE ORAȘUL</div>
    <div class="field" style="left:581px;width:196px">BUCUREȘTI<svg width="12" height="9" viewBox="0 0 12 9"><path d="M0 0H12L6 9Z" fill="#555"/></svg></div>
    <div class="btn-show">AFIȘEAZĂ<br>RESTAURANTE</div>
  </form>

  <div class="section-head"></div>
  <h2 class="section-pill">RESTAURANTE PARTENERE</h2>

  <section class="partners">
    <div class="partner"><div class="thumb" role="img" aria-label="Fotografie restaurant"></div><div class="name">La Ceaunul Vesel</div><div class="cuisine">Romanesc</div></div>
    <div class="partner"><div class="thumb" role="img" aria-label="Fotografie restaurant"></div><div class="name">Cantina Solei</div><div class="cuisine">Italian</div></div>
    <div class="partner"><div class="thumb" role="img" aria-label="Fotografie restaurant"></div><div class="name">the PALETTE</div><div class="cuisine">Contemporan</div></div>
    <div class="partner"><div class="thumb" role="img" aria-label="Fotografie restaurant"></div><div class="name">Montebello</div><div class="cuisine">Italian</div></div>
    <div class="partner"><div class="thumb" role="img" aria-label="Fotografie restaurant"></div><div class="name">Carolina</div><div class="cuisine">Mixt</div></div>
    <div class="partner"><div class="thumb" role="img" aria-label="Fotografie restaurant"></div><div class="name">Stone Road Cafe</div><div class="cuisine">American, European</div></div>
    <div class="partner"><div class="thumb" role="img" aria-label="Fotografie restaurant"></div><div class="name">Boviro</div><div class="cuisine">Grill</div></div>
    <div class="partner"><div class="thumb" role="img" aria-label="Fotografie restaurant"></div><div class="name">Nordic Bean Shop</div><div class="cuisine">Cafenea</div></div>
    <div class="partner"><div class="thumb" role="img" aria-label="Fotografie restaurant"></div><div class="name">Tiramola Ristorante</div><div class="cuisine">Italian</div></div>
    <div class="partner"><div class="thumb" role="img" aria-label="Fotografie restaurant"></div><div class="name">Petit Bistro</div><div class="cuisine">Francez</div></div>
    <div class="partner"><div class="thumb" role="img" aria-label="Fotografie restaurant"></div><div class="name">Casa Ulmilor</div><div class="cuisine">Romanesc</div></div>
    <div class="partner"><div class="thumb" role="img" aria-label="Fotografie restaurant"></div><div class="name">OLMO</div><div class="cuisine">Spaniol</div></div>
    <div class="partner"><div class="thumb" role="img" aria-label="Fotografie restaurant"></div><div class="name">Zarva</div><div class="cuisine">Romanesc</div></div>
    <div class="partner"><div class="thumb" role="img" aria-label="Fotografie restaurant"></div><div class="name">Gradina Lunii</div><div class="cuisine">Vegetarian</div></div>
    <div class="partner"><div class="thumb" role="img" aria-label="Fotografie restaurant"></div><div class="name">Simfora</div><div class="cuisine">Cafenea</div></div>
  </section>
</main>

<footer class="footer">
  <nav class="footer-nav">Contactează-ne<span>|</span>Despre noi<span>|</span>Partenerii noștri<span>|</span>FAQ<span>|</span>Devino partener</nav>
  <div class="copyright">Copyright © 2013 gustino.ro. Toate drepturile rezervate.</div>
</footer>
</body>
</html>
```